Quintel Packaging Business Card

Project Overview
We are seeking a modern, minimalist business card that effectively represents our company while making a bold and lasting impression. The design should reflect trust, professionalism, and innovation, reinforcing our expertise in custom plastic manufacturing for warehouse and distribution centers.

Provided Assets & Specifications
Logo: We will provide our official logo for integration into the design.
Design Files: Photoshop (PSD) files for our printing specifications will be supplied.

Card Size & Material:
Dimensions: 3.5" x 2"
Material: 1/8" Radius Plastic Business Cards with 1/8" Rounded Corners
Clear plastic background—the design should strategically incorporate transparency.
Orientation: The card should be designed in landscape format for a sleek and professional presentation.

Design Requirements:
Logo Prominence
The logo must be the focal point of the card.
Space should be used effectively to draw attention to the logo while maintaining a minimalist layout.

Clear Plastic Integration
The transparent background should create the illusion of blank space, enhancing the modern and high-quality feel.
Avoid any frosted effects—we do not want white areas to appear semi-transparent.

Minimalist & Impactful
Clean, structured, and easy to read at a glance.
Focus on sharp contrast to ensure legibility and visibility.
The design should instill confidence and reflect our role as a leading plastics manufacturer.

Color Palette & Contrast
Primary Colors: Blue, Black, White, and Grey
Use bold black or blue for text and key elements to ensure they stand out against the clear plastic.
Avoid light, pastel, or neon colors that may fade into the plastic background.
No frosted or semi-transparent white—we do not want a cloudy effect.

Typography & Information Hierarchy
Bold, modern typography—clear, professional, and highly legible.
The business card should highlight:
Company Logo (Primary Focus)
Full Name & Title
Phone Number
Email
Website

Brand Representation
The card should reflect our expertise in manufacturing high-quality custom plastics for large-scale packaging and distribution businesses.
Our clients rely on us to enhance their brand presence through custom plastic solutions, and our business cards should reinforce that sense of precision and trust.

Final Considerations
Utilize the clear plastic effectively to differentiate our brand from standard business cards.
Maintain a sleek, professional aesthetic while ensuring all text and elements remain legible.
The design should align with our industry, conveying reliability and innovation.
We look forward to seeing a design that captures our brand identity, maximizes the clear plastic medium, and makes a strong, professional impact on our clients.

```html
<!DOCTYPE html>
<html lang="en">
<head>
<meta charset="utf-8">
<title>Quintel Packaging Business Card</title>
<link href="https://fonts.googleapis.com/css2?family=Montserrat:wght@400;500;700&display=swap" rel="stylesheet">
<style>
  :root{
    --bg:#d3d8d8;
    --card:#f4f4f3;
    --blue:#1b8fcb;
    --ink:#2f2f30;
    --edge:#c9cccc;
  }
  *{box-sizing:border-box;margin:0;padding:0}
  html,body{width:1200px;height:881px;overflow:hidden}
  body{background:var(--bg);font-family:"Montserrat",Arial,sans-serif;color:var(--ink);position:relative}
  .card{
    position:absolute;left:270px;width:660px;height:377px;
    background:var(--card);border:1px solid var(--edge);border-radius:10px;
    border-bottom:4px solid var(--blue);
  }
  .card--front{top:40px}
  .card--back{top:461px}

  /* front */
  .brand{position:absolute;display:flex;align-items:center;gap:12px}
  .brand__mark{background:var(--ink);flex:none}
  .brand__name{font-weight:700;color:var(--ink);white-space:nowrap;letter-spacing:.01em}
  .card--front .brand{left:44px;top:160px}
  .card--front .brand__mark{width:24px;height:24px}
  .card--front .brand__name{font-size:23px}

  .divider{position:absolute;left:318px;top:80px;width:2px;height:220px;background:var(--blue)}
  .details{position:absolute;left:344px;top:84px;font-size:15px;line-height:1.45}
  .details__name{font-weight:700;color:var(--blue);font-size:25px;letter-spacing:.03em;text-transform:uppercase;line-height:1.2}
  .details__title{font-size:15px;margin-bottom:8px}
  .details__address{margin-bottom:8px}
  .contact{display:flex;align-items:center;gap:9px}
  .contact svg{width:13px;height:13px;fill:var(--blue);flex:none}

  /* back */
  .card--back .brand{left:50%;top:50%;transform:translate(-50%,-50%);gap:20px}
  .card--back .brand__mark{width:46px;height:46px}
  .card--back .brand__name{font-size:44px}
</style>
</head>
<body>
  <section class="card card--front">
    <div class="brand">
      <span class="brand__mark"></span>
      <span class="brand__name">Quintel Packaging</span>
    </div>
    <div class="divider"></div>
    <div class="details">
      <p class="details__name">Daniel Hart</p>
      <p class="details__title">Managing Director</p>
      <p class="details__address">Your address, City<br>State, Zip 1234</p>
      <p class="contact">
        <svg viewBox="0 0 24 24"><path d="M6.6 10.8a15 15 0 0 0 6.6 6.6l2.2-2.2a1 1 0 0 1 1-.25 11.4 11.4 0 0 0 3.6.57 1 1 0 0 1 1 1V20a1 1 0 0 1-1 1A17 17 0 0 1 3 4a1 1 0 0 1 1-1h3.5a1 1 0 0 1 1 1c0 1.25.2 2.45.57 3.57a1 1 0 0 1-.25 1z"/></svg>
        123 456 789
      </p>
      <p class="contact">
        <svg viewBox="0 0 24 24"><path d="M2 5h20v14H2z M2 5l10 8 10-8" /><path d="M3 6l9 7 9-7v-.5H3z" fill="#f4f4f3"/></svg>
        info@yourgmail.com
      </p>
      <p class="contact">
        <svg viewBox="0 0 24 24"><circle cx="12" cy="12" r="10"/><path d="M2 12h20M12 2c3 3 3 17 0 20M12 2c-3 3-3 17 0 20" stroke="#f4f4f3" stroke-width="1.4" fill="none"/></svg>
        www.yourwebsite.com
      </p>
    </div>
  </section>

  <section class="card card--back">
    <div class="brand">
      <span class="brand__mark"></span>
      <span class="brand__name">Quintel Packaging</span>
    </div>
  </section>
</body>
</html>
```